Business card for a new innovative and professional lawn care business

We need a business card design for a new lawn care business in Halifax NS Canada. We offer lawn services in Halifax & Bedford. Our services offered include lawn care, garden services, and property maintenance. We take pride in our work and are experienced at what we do. I would like to see a design that is double sided. On the backside I would like the something simple (maybe my logo preferably on blackround (linked below) with website link, Facebook page or something). The front I want to include contact info:
Morgan Pell
phone 902-555-0148
email - brookvaleyards.ca
facebook - Facebook.com/brookvaleyards
Instagram maybe ? - instagram.com/brookvaleyard
Serving Halifax and Bedford for 5 years?
I don't want it to have too much information as I will be passing them out in aim to visit website, or call !
We do want it to include lawn care, garden services and property maintenance.
Basic, catchy, and modern looking !
Logo attached below !

Target Market(s)

Passing business cards to everyone I meet or interact with.

Industry/Entity Type

Lawn Care

Contact Information for Business Card

Double sided with some basic information, with catchy colours and easy to look at.

Font styles to use
Sans Serif

Requirements
Must have
• Must be double sided and have :
• Name, Phone, Email, FB, Website, and 3 main services offered - lawn care, property maintenance, garden services
Nice to have
• Would be nice to have instagram link if it goes well on there
Should not have
• Don't want too much writing or images that are distracting

```html
<!DOCTYPE html>
<html lang="en">
<head>
<meta charset="utf-8">
<title>Brookvale Yards – Business Card</title>
<link rel="stylesheet" href="https://fonts.googleapis.com/css2?family=Open+Sans:wght@400;600;700;800&display=swap">
<style>
  :root {
    --green-dark: #1f7a35;
    --green-mid: #2e9440;
    --green-light: #8cc63f;
    --mower-tint: #e6efe8;
    --paper: #ffffff;
    --stage: #e9ebe9;
    --ink: #1f6a30;
  }
  * { box-sizing: border-box; margin: 0; padding: 0; }
  html, body { width: 1200px; height: 900px; overflow: hidden; }
  body {
    background: var(--stage);
    font-family: "Open Sans", Arial, sans-serif;
    position: relative;
  }
  .card {
    position: absolute;
    left: 250px;
    width: 700px;
    height: 400px;
    background: var(--paper);
    border-radius: 22px;
    overflow: hidden;
    box-shadow: 0 6px 18px rgba(0,0,0,.12);
  }
  .card--back { top: 35px; }
  .card--front { top: 465px; }

  /* Back side */
  .brand {
    color: var(--green-dark);
    font-weight: 800;
    letter-spacing: 2px;
    text-transform: uppercase;
    display: flex;
    align-items: center;
    gap: 14px;
    white-space: nowrap;
  }
  .brand__dot {
    width: 18px; height: 18px; border-radius: 50%;
    background: var(--green-light);
    flex: none;
  }
  .card--back .brand {
    position: absolute;
    left: 0; right: 0; top: 140px;
    justify-content: center;
    font-size: 50px;
  }
  .socials {
    position: absolute;
    left: 40px; right: 40px; bottom: 32px;
    display: flex;
    justify-content: space-between;
    color: var(--green-dark);
    font-size: 18px;
    font-weight: 600;
    white-space: nowrap;
  }
  .social { display: flex; align-items: center; gap: 10px; }
  .social__mark {
    width: 16px; height: 16px; border-radius: 3px;
    background: var(--green-light);
    flex: none;
  }

  /* Front side */
  .side-band { position: absolute; left: 0; top: 0; }
  .card--front .brand {
    position: absolute;
    left: 70px; top: 40px;
    font-size: 40px;
  }
  .holder {
    position: absolute;
    left: 70px; top: 128px;
    color: var(--green-dark);
    font-size: 30px;
    font-weight: 800;
    text-transform: uppercase;
    white-space: nowrap;
  }
  .contacts {
    position: absolute;
    left: 70px; top: 178px;
    list-style: none;
    color: var(--ink);
    font-size: 18px;
    font-weight: 600;
    line-height: 27px;
    white-space: nowrap;
  }
  .contacts li { display: flex; align-items: center; gap: 10px; }
  .contacts svg { width: 14px; height: 14px; flex: none; }
  .services {
    position: absolute;
    left: 70px; top: 268px;
  }
  .services__title {
    color: var(--green-light);
    font-size: 20px;
    font-weight: 800;
    letter-spacing: 1px;
    line-height: 28px;
  }
  .services__list {
    list-style: none;
    color: var(--green-dark);
    font-size: 18px;
    font-weight: 600;
    line-height: 25px;
    white-space: nowrap;
  }
  .services__list li::before {
    content: "";
    display: inline-block;
    width: 8px; height: 8px; border-radius: 50%;
    background: var(--green-light);
    margin-right: 10px;
    vertical-align: middle;
  }
  .rule {
    position: absolute;
    left: 250px; right: 0; top: 282px;
    height: 2px;
    background: var(--green-light);
  }
  .mower-art {
    position: absolute;
    right: 30px; top: 20px;
    width: 290px; height: 340px;
    border-radius: 30px;
    background: radial-gradient(ellipse at 50% 60%, var(--mower-tint), rgba(230,239,232,0) 70%);
  }
</style>
</head>
<body>

  <section class="card card--back" aria-label="Card back">
    <div class="brand"><span class="brand__dot"></span>Brookvale Yards</div>
    <div class="socials">
      <span class="social"><span class="social__mark"></span>friendpage.ca/brookvaleyards</span>
      <span class="social"><span class="social__mark"></span>snapwall.ca/brookvaleyard</span>
    </div>
  </section>

  <section class="card card--front" aria-label="Card front">
    <svg class="side-band" width="40" height="400" viewBox="0 0 40 400">
      <polygon points="0,0 28,0 28,140 38,160 38,400 0,400" fill="var(--green-dark)"/>
      <polygon points="28,0 36,0 36,135 28,140" fill="var(--green-light)"/>
    </svg>
    <div class="mower-art" role="img" aria-label="Faint lawn mower illustration"></div>
    <div class="rule"></div>

    <div class="brand">Brookvale Yards</div>
    <h1 class="holder">Morgan Pell</h1>
    <ul class="contacts">
      <li>
        <svg viewBox="0 0 24 24"><path fill="var(--green-light)" d="M6.6 10.8a15 15 0 0 0 6.6 6.6l2.2-2.2a1 1 0 0 1 1-.25 11.4 11.4 0 0 0 3.6.57 1 1 0 0 1 1 1V20a1 1 0 0 1-1 1A17 17 0 0 1 3 4a1 1 0 0 1 1-1h3.5a1 1 0 0 1 1 1c0 1.25.2 2.45.57 3.57a1 1 0 0 1-.25 1z"/></svg>
        902-555-0148
      </li>
      <li>
        <svg viewBox="0 0 24 24"><rect x="2" y="5" width="20" height="14" rx="1" fill="none" stroke="var(--green-light)" stroke-width="2"/><path d="M2 6l10 7 10-7" fill="none" stroke="var(--green-light)" stroke-width="2"/></svg>
        info@brookvaleyards.ca
      </li>
      <li>
        <svg viewBox="0 0 24 24"><circle cx="12" cy="12" r="10" fill="none" stroke="var(--green-light)" stroke-width="2"/><path d="M2 12h20M12 2c3 3 3 17 0 20M12 2c-3 3-3 17 0 20" fill="none" stroke="var(--green-light)" stroke-width="2"/></svg>
        www.brookvaleyards.ca
      </li>
    </ul>
    <div class="services">
      <h2 class="services__title">SERVICES</h2>
      <ul class="services__list">
        <li>Lawn care</li>
        <li>Garden services</li>
        <li>Property maintenance</li>
      </ul>
    </div>
  </section>

</body>
</html>
```